Business Card Design for Vintage Jazz

I am a vintage jazz band leader in New York City. My groups play the music of the 1920s, 1930s and 1940s. My website is morvalquist.com for more info on what I do.

I am looking for a two sided business card design that has the look and feel of a really nice business card from the 1930s. I need to convey with the design that my work has that vintage kind of class and style, but also conveys that we are fun and entertaining.

Most importantly it should make a bold staement. If Hal Denbrook had a card, what would it have looked like? I want a card that I feel confident will make an impact and will let people know that my work is te the top that NYC has to offer in vintage jazz..

Note that I have only decided to avoid the "committed payment" option as I have not used this service before. Assuming that I get quality work I will select a design from those presented.

Target Market(s)

people who want to hire my band for events, media, and new fans of the band

Industry/Entity Type

Performing Art

Contact Information for Business Card

Definitely a matte finish, possibly a sort of old style of paper with that brown tint? definitely a thick card.

Requirements
Must have
• FRONT
• My name: Tobin Vashley
• What I do: Bandleader, Guitarist, Vocalist, Songwriter
• Contact Details: morvalquist.com tobin@morvalquist.com 646-555-0148
• BACK
• My Social Media Links:
• facebook.morvalquist.com
• twitter, instagram, linkedin: morvalquist
• I'm also including a photo image I would like to use. The photo's background is not needed, and to be honest isn't really desireable. Just looking to use the image of me.
Nice to have
• I'm attaching which could be used as is, omitted from the card, or altered maybe with text going around the outside of the circle or in some other way. It may need some clean up to the edges of the lettering as we only use it for the website thumbnail.
• If there's space I'd like to include the text "join our mailing list for a free song download: freesong.morvalquist.com" If not perhaps just "Download a Free Song at: freesong.morvalquist.com - something to this end.
Should not have
• anything cartoony. Don't think retro 90s's vision of the swing era, think actual swing era!
• anything modern. Got to look old school
• Try to avoid dark backgrounds. Since we often play in bars and clubs where it is dar, a d
• avoid script fonts.

```html
<!DOCTYPE html>
<html lang="en">
<head>
<meta charset="utf-8">
<title>Tobin Vashley — Business Card</title>
<link rel="stylesheet" href="https://fonts.googleapis.com/css2?family=Open+Sans:wght@400;600;700&display=swap">
<style>
  :root {
    --stage: #2b2b2d;
    --teal: #5fc0a9;
    --teal-light: #79cdb9;
    --teal-deep: #4fb29b;
    --white: #ffffff;
    --paper: #f6f6f4;
    --ink: #3f4042;
    --ink-soft: #5a5b5d;
    --icon-dark: #1f2a28;
    --photo-dark: #3a3a3a;
    --photo-light: #bdbdbd;
  }
  * { margin: 0; padding: 0; box-sizing: border-box; }
  html, body {
    width: 1200px; height: 795px; overflow: hidden;
    background: var(--stage);
    font-family: "Open Sans", Arial, sans-serif;
  }
  .sheet {
    position: relative; width: 1200px; height: 795px;
    display: flex; align-items: center; justify-content: center; gap: 30px;
  }
  .card {
    position: relative; width: 555px; height: 318px;
    border-radius: 22px; overflow: hidden;
  }

  /* Front side */
  .card--front {
    background: linear-gradient(120deg, var(--teal-deep) 0%, var(--teal) 55%, var(--teal-light) 100%);
  }
  .portrait {
    position: absolute; left: 38px; bottom: 0; width: 230px; height: 290px;
    border-radius: 110px 110px 0 0;
    background: linear-gradient(180deg, var(--photo-light) 0%, var(--photo-dark) 70%);
  }
  .front-text {
    position: absolute; right: 34px; top: 64px; width: 270px;
    text-align: center; color: var(--white);
  }
  .front-name { font-size: 40px; font-weight: 700; line-height: 1; letter-spacing: 0.2px; }
  .front-role { font-size: 13px; margin-top: 6px; }
  .social-row { display: flex; justify-content: center; gap: 8px; margin-top: 12px; }
  .social-dot { width: 20px; height: 20px; border-radius: 50%; background: var(--icon-dark); }
  .front-url { font-size: 14px; letter-spacing: 3.5px; margin-top: 12px; }

  /* Back side */
  .card--back { background: var(--paper); text-align: center; color: var(--ink); }
  .monogram {
    width: 78px; height: 78px; border-radius: 50%;
    background: var(--teal); margin: 54px auto 0;
    display: flex; align-items: center; justify-content: center;
    font-size: 30px; font-weight: 600; color: var(--icon-dark);
  }
  .back-name { font-size: 38px; font-weight: 700; color: var(--teal); margin-top: 8px; line-height: 1.1; }
  .back-role { font-size: 15px; letter-spacing: 1px; text-transform: uppercase; color: var(--ink-soft); margin-top: 6px; word-spacing: 6px; }
  .contact-row {
    display: flex; justify-content: center; align-items: center; gap: 12px;
    margin-top: 18px; font-size: 14px; color: var(--ink);
  }
  .contact-item { display: flex; align-items: center; gap: 4px; }
  .contact-icon { width: 14px; height: 14px; flex: none; }
</style>
</head>
<body>
<main class="sheet">
  <section class="card card--front" aria-label="Card front">
    <div class="portrait" role="img" aria-label="Black and white photo of the bandleader in a white-trimmed blazer tipping a straw boater hat"></div>
    <div class="front-text">
      <h1 class="front-name">Tobin Vashley</h1>
      <p class="front-role">Bandleader, Guitarist, Vocalist, Songwriter</p>
      <div class="social-row" aria-label="Social media links">
        <span class="social-dot"></span><span class="social-dot"></span><span class="social-dot"></span><span class="social-dot"></span>
        <span class="social-dot"></span><span class="social-dot"></span><span class="social-dot"></span><span class="social-dot"></span>
      </div>
      <p class="front-url">www.morvalquist.com</p>
    </div>
  </section>

  <section class="card card--back" aria-label="Card back">
    <div class="monogram">TV</div>
    <h2 class="back-name">Tobin Vashley</h2>
    <p class="back-role">Bandleader, Guitarist, Vocalist, Songwriter</p>
    <div class="contact-row">
      <span class="contact-item">
        <svg class="contact-icon" viewBox="0 0 14 14"><circle cx="7" cy="7" r="7" fill="#5fc0a9"/><path d="M4.5 3.5l1.5 0 .6 2-1 .8a5 5 0 0 0 2.1 2.1l.8-1 2 .6 0 1.5c-3.5.3-6.3-2.5-6-6z" fill="#fff"/></svg>
        646-555-0148
      </span>
      <span class="contact-item">
        <svg class="contact-icon" viewBox="0 0 14 14"><circle cx="7" cy="7" r="7" fill="#5fc0a9"/><rect x="3.5" y="4.5" width="7" height="5" fill="none" stroke="#fff" stroke-width="1"/><path d="M3.5 4.5l3.5 3 3.5-3" fill="none" stroke="#fff" stroke-width="1"/></svg>
        tobin@morvalquist.com
      </span>
      <span class="contact-item">
        <svg class="contact-icon" viewBox="0 0 14 14"><circle cx="7" cy="7" r="7" fill="#5fc0a9"/><circle cx="7" cy="7" r="4" fill="none" stroke="#fff" stroke-width="1"/><ellipse cx="7" cy="7" rx="1.8" ry="4" fill="none" stroke="#fff" stroke-width="1"/><path d="M3 7h8" stroke="#fff" stroke-width="1"/></svg>
        www.morvalquist.com
      </span>
    </div>
  </section>
</main>
</body>
</html>
```